Meadowlark Property Review is a leading provider of residential appraisal and home inspection products in S

I need a business card/logo designed that obviously describes my business. We are a residential appraisal and home inspection company in Springfield, MO. We offer residential appraisals, home inspection, pest inspection and radon gas measurement. We have been in business for 18 years and hold state certified residential appraisal licenses and OBREX certified home inspection licenses. I have a logo that I really like and will attach, but would be open to new suggestions. I like more modern designs than traditional and would like a two sided card with our services, licenses and qualifications on the back.

```html
<!DOCTYPE html>
<html lang="en">
<head>
<meta charset="utf-8">
<title>Meadowlark Property Review – Business Card</title>
<link rel="stylesheet" href="https://fonts.googleapis.com/css2?family=Source+Sans+3:ital,wght@0,400;0,600;1,400&display=swap">
<style>
  :root {
    --bg: #3b3b3b;
    --brown: #8b6a41;
    --orange: #f08a1d;
    --paper: #f7f7f7;
    --ink: #454545;
    --white: #ffffff;
  }
  * { margin: 0; padding: 0; box-sizing: border-box; }
  html, body { width: 1200px; height: 750px; overflow: hidden; }
  body {
    background: var(--bg);
    font-family: "Source Sans 3", sans-serif;
    position: relative;
  }
  .card {
    position: absolute;
    top: 228px;
    width: 462px;
    height: 262px;
    overflow: hidden;
  }
  .card-front { left: 124px; background: var(--paper); }
  .card-back { left: 618px; background: var(--brown); }

  .front-band { position: absolute; left: 0; top: 0; width: 462px; height: 100px; }
  .holder { position: absolute; left: 0; top: 14px; width: 470px; text-align: center; color: var(--white); }
  .holder-name { font-size: 16px; font-weight: 600; line-height: 20px; }
  .holder-title { font-size: 12px; line-height: 16px; }

  .brand {
    position: absolute; left: 40px; top: 150px; width: 180px;
    display: flex; align-items: center; gap: 8px;
    color: var(--brown); font-size: 15px; font-weight: 600; line-height: 18px;
  }
  .brand-square { width: 14px; height: 14px; background: var(--orange); flex: none; }

  .contact { position: absolute; left: 258px; top: 110px; color: var(--ink); font-size: 10.5px; line-height: 14px; }
  .address { margin-bottom: 8px; }
  .contact-row { display: flex; align-items: center; gap: 7px; height: 17.5px; }
  .contact-row svg { width: 12px; height: 12px; flex: none; }

  .back-name {
    position: absolute; left: 0; top: 98px; width: 462px; text-align: center;
    color: var(--white); font-size: 20px; font-weight: 600;
  }
  .services {
    position: absolute; left: 0; top: 200px; width: 462px; text-align: center;
    color: var(--white); font-size: 12px; font-style: italic; line-height: 18px;
  }
  .dot { color: var(--orange); }
</style>
</head>
<body>
  <section class="card card-front">
    <svg class="front-band" viewBox="0 0 462 100" aria-hidden="true">
      <path d="M0 0 H462 V88 Q231 54 0 88 Z" fill="var(--brown)"/>
      <path d="M24 84 Q130 66 240 66" fill="none" stroke="var(--paper)" stroke-width="1.2"/>
      <path d="M240 66 Q360 66 440 80" fill="none" stroke="var(--orange)" stroke-width="4" stroke-linecap="round"/>
    </svg>
    <div class="holder">
      <div class="holder-name">Dana Whitfield</div>
      <div class="holder-title">CEO/Founder</div>
    </div>

    <div class="brand">
      <span class="brand-square"></span>
      <span>Meadowlark Property Review</span>
    </div>

    <div class="contact">
      <div class="address">412 Larkspur Court<br>Springfield, Missouri 65804</div>
      <div class="contact-row">
        <svg viewBox="0 0 12 12" aria-hidden="true"><path d="M2 1 L4 1 L5 4 L3.6 5 Q4.8 7.4 7 8.4 L8 7 L11 8 L11 10 Q10 11 8.5 11 Q2.5 9.5 1 3.5 Q1 2 2 1 Z" fill="var(--ink)"/></svg>
        <span>417 555 0182</span>
      </div>
      <div class="contact-row">
        <svg viewBox="0 0 12 12" aria-hidden="true"><rect x="3" y="1" width="6" height="3" fill="var(--ink)"/><rect x="1" y="4.5" width="10" height="5" rx="1" fill="var(--ink)"/><rect x="3" y="8" width="6" height="3" fill="var(--ink)" stroke="var(--paper)" stroke-width="0.8"/></svg>
        <span>417 555 0196</span>
      </div>
      <div class="contact-row">
        <svg viewBox="0 0 12 12" aria-hidden="true"><rect x="1" y="2.5" width="10" height="7" fill="var(--ink)"/><path d="M1 2.8 L6 6.5 L11 2.8" fill="none" stroke="var(--paper)" stroke-width="0.9"/></svg>
        <span>office@meadowlark.com</span>
      </div>
      <div class="contact-row">
        <svg viewBox="0 0 12 12" aria-hidden="true"><circle cx="6" cy="6" r="5" fill="var(--ink)"/><path d="M3 3.5 Q5 4 4.5 6 Q6.5 7 5.5 9.5 M8 2.5 Q7 4.5 9 5" fill="none" stroke="var(--paper)" stroke-width="0.9"/></svg>
        <span>www.meadowlark.com</span>
      </div>
    </div>
  </section>

  <section class="card card-back">
    <div class="back-name">Meadowlark Property Review</div>
    <p class="services">
      Residential appraisals <span class="dot">&#9679;</span> Home inspection<br>
      Pest inspection and radon gas measurement.
    </p>
  </section>
</body>
</html>
```